Meridale Nutrition needs Stationary and a business card

We would like to use our current logo. The text can be moved around as needed. The stationary needs to be a 'first page' where the logo is more prominent to be impressive on higher quality paper and a second page where the logo is more subtle where there will be much more information on the page. There are 2 clinic locations which will need include name, address, phone number, fax number, web address. The business card should be single sided and contain this information also.
The design must be contemporary and sophisticated as this is a science based diet run out of a medical clinic.

Target Market(s)

People wanting to lose weight, athletes looking to optimise performance, people with arthritis or fighting cancer

Industry/Entity Type

Business

Contact Information for Business Card

must use the logo. I have attached an example card with the practice details on it. there must be space for the doctors name. Also the website www.meridalenutrition.com.au

Requirements
Must have
• the logo, the business adresses and phone numbers, the website, the doctors name and qualifications
Nice to have
• some creativity
Should not have
• Do not simply reproduce the existing card please

```html
<!DOCTYPE html>
<html lang="en">
<head>
<meta charset="utf-8">
<title>Meridale Nutrition — Business Card</title>
<link href="https://fonts.googleapis.com/css2?family=Arimo:wght@400;700&display=swap" rel="stylesheet">
<style>
  :root {
    --backdrop: #e9e6e1;
    --sky: #2bc3f3;
    --paper: #ffffff;
    --brand-navy: #2a5d97;
    --accent-blue: #23b0e8;
    --ink-grey: #6f7378;
    --divider: #dfe3e7;
  }
  * { box-sizing: border-box; margin: 0; padding: 0; }
  html, body {
    width: 1200px; height: 950px; overflow: hidden;
    background: var(--backdrop);
    font-family: "Arimo", Arial, sans-serif;
  }
  .sheet { position: relative; width: 1200px; height: 950px; }

  .card {
    position: absolute;
    width: 660px; height: 400px;
    left: 270px;
    border-radius: 4px;
    box-shadow: 0 6px 18px rgba(0,0,0,0.12);
    overflow: hidden;
  }

  /* reverse side */
  .card--reverse { top: 45px; background: var(--sky); }
  .card--reverse .brand {
    position: absolute; left: 0; right: 0; top: 100px;
    display: flex; flex-direction: column; align-items: center;
  }
  .card--reverse .brand-dot {
    width: 110px; height: 110px; border-radius: 50%;
    background: var(--paper); margin-bottom: 22px;
  }
  .card--reverse .brand-name {
    color: var(--paper); font-weight: 700; font-size: 30px;
    letter-spacing: 1px; text-transform: uppercase;
    padding: 6px 4px; border-top: 2px solid var(--paper); border-bottom: 2px solid var(--paper);
  }
  .card--reverse .brand-web {
    color: var(--paper); font-size: 15px; letter-spacing: 1px; margin-top: 14px;
  }

  /* front side */
  .card--front { top: 505px; background: var(--paper); }
  .card--front .identity {
    position: absolute; left: 0; top: 0; width: 52%; height: 100%;
    display: flex; flex-direction: column; align-items: center; justify-content: center;
    text-align: center; padding: 0 16px;
  }
  .identity .brand-dot {
    width: 100px; height: 100px; border-radius: 50%;
    background: var(--accent-blue); margin-bottom: 14px;
  }
  .identity .brand-name {
    color: var(--brand-navy); font-weight: 700; font-size: 24px;
    letter-spacing: 0.5px; text-transform: uppercase;
    padding-bottom: 6px; border-bottom: 2px solid var(--accent-blue); margin-bottom: 12px;
  }
  .identity .doctor-name {
    color: var(--brand-navy); font-size: 22px; font-weight: 400; margin-bottom: 8px;
  }
  .identity .credentials, .identity .specialty {
    color: var(--accent-blue); font-size: 13px; line-height: 1.4;
  }
  .identity .brand-web {
    color: var(--brand-navy); font-size: 13px; font-weight: 700; margin-top: 12px;
  }

  .card--front .divider {
    position: absolute; left: 52%; top: 0; width: 1px; height: 100%;
    background: var(--divider);
  }

  .card--front .clinics {
    position: absolute; left: 57%; top: 36px; right: 20px;
    font-size: 14px; line-height: 1.35; color: var(--ink-grey);
  }
  .clinic { margin-bottom: 12px; }
  .clinic-name { color: var(--brand-navy); font-weight: 700; }
  .clinic-contact strong { color: var(--brand-navy); }
  .services p { margin: 0; }
</style>
</head>
<body>
<main class="sheet">

  <section class="card card--reverse" aria-label="Card reverse">
    <div class="brand">
      <span class="brand-dot"></span>
      <span class="brand-name">Meridale Nutrition</span>
      <span class="brand-web">www.meridalenutrition.com.au</span>
    </div>
  </section>

  <section class="card card--front" aria-label="Card front">
    <div class="identity">
      <span class="brand-dot"></span>
      <span class="brand-name">Meridale Nutrition</span>
      <h1 class="doctor-name">Dr Elias Varnum</h1>
      <p class="credentials">MBBS (NSW) MBiomedE FRACS (Ortho) FAOrthA</p>
      <p class="specialty">Orthopaedic Surgeon</p>
      <p class="brand-web">www.meridalenutrition.com.au</p>
    </div>

    <div class="divider"></div>

    <div class="clinics">
      <div class="clinic">
        <div class="clinic-name">Hollis</div>
        <div>12-14 Ashgrove Road</div>
        <div>Hollis NSW 2139</div>
        <div class="clinic-contact"><strong>Tel:</strong> 02 9555 0142</div>
        <div class="clinic-contact"><strong>Fax:</strong> 02 9555 0143</div>
      </div>
      <div class="clinic">
        <div class="clinic-name">Kelbury</div>
        <div>88 Marlow Street</div>
        <div>Kelbury NSW 2034</div>
        <div class="clinic-contact"><strong>Tel:</strong> 02 9555 0187</div>
        <div class="clinic-contact"><strong>Fax:</strong> 02 9555 0188</div>
      </div>
      <div class="services">
        <p>Shoulder and Elbow</p>
        <p>www.varnumortho.com.au</p>
        <p>Knee surgery</p>
        <p>www.jointcareclinic.com.au</p>
      </div>
    </div>
  </section>

</main>
</body>
</html>
```